Shopping centre customer engagement software website

We need a multi page site with :

*What we do.
*How it works.
*Benefits
* Case study
* Testimonial
* Business login (we provide link to business portal)
* Consumer login (we provide link to consumer site)
* Book a demo
* Contact us

We want it to be clean and crisp and very self explanatory with little clutter. We are thinking white but are open to what ever looks the best.
Updates

Wordpress is preferred

Need extra days to review

Target Market(s)

Shopping centre managers and retail property companies

Coding

Coded - Design and coding required

Number of Pages Required

5+ page

Font styles to use
Sans Serif

Colors
ffffff

Requirements
Must have
• As listed above and must be responsive! Checkout our existing site for the text to be included (will be edited but it’ll give you an idea) www.vostrelink.com

```html
<!DOCTYPE html>
<html lang="en">
<head>
<meta charset="utf-8">
<title>Vostrelink – Shopping Centre Engagement</title>
<link href="https://fonts.googleapis.com/css2?family=Poppins:ital,wght@0,400;0,500;0,600;0,700;1,400&display=swap" rel="stylesheet">
<style>
:root{
  --blue:#2c47a6;
  --blue-dark:#243c93;
  --sky:#36a3ee;
  --ink:#1d1f24;
  --body:#4a4f57;
  --muted:#8a9099;
  --line:#d5dae1;
  --mist:#eef1f6;
  --red:#f0574a;
  --teal:#3d6472;
  --white:#ffffff;
}
*{box-sizing:border-box;margin:0;padding:0}
html,body{width:1200px;height:4027px;overflow:hidden}
body{font-family:"Poppins",sans-serif;color:var(--body);background:var(--white);position:relative}
section,header,footer{position:absolute;left:0;width:1200px}
.abs{position:absolute}
.section-title{position:absolute;left:0;width:1200px;text-align:center;font-size:21px;font-weight:700;color:var(--ink);letter-spacing:.3px}
.pill{position:absolute;display:flex;align-items:center;gap:10px;background:var(--blue);color:var(--white);border-radius:22px;font-size:13px;font-weight:500;padding:0 8px 0 22px;height:38px}
.pill .arrow{width:24px;height:24px;border-radius:50%;background:var(--sky);display:flex;align-items:center;justify-content:center}

/* header */
.site-header{top:0;height:130px;background:var(--white)}
.brand-name{left:160px;top:46px;font-size:22px;font-weight:500;color:#4b5260;letter-spacing:3px}
.header-phone{left:725px;top:30px;font-size:17px;font-weight:600;color:var(--sky);display:flex;gap:8px;align-items:center}
.login{left:944px;top:26px;width:94px;height:36px;border-radius:18px;background:var(--blue);color:var(--white);font-size:12px;font-weight:600;display:flex;align-items:center;justify-content:center}
.main-nav{left:418px;top:86px;display:flex;gap:40px;font-size:14px;color:var(--ink)}

/* hero */
.hero{top:130px;height:475px;background:linear-gradient(180deg,#9aa0a6 0%,#c9ccd0 45%,#e4e6e8 75%,#c7c9cc 100%)}
.hero-photo{position:absolute;inset:0}
.hero h1{position:absolute;top:185px;left:0;width:1200px;text-align:center;color:var(--white);font-size:42px;font-weight:700}
.hero p{position:absolute;top:250px;left:360px;width:620px;text-align:center;color:var(--white);font-size:21px;line-height:30px}
.hero-dots{position:absolute;top:442px;left:538px;display:flex;gap:8px}
.hero-dots span{width:26px;height:5px;background:rgba(255,255,255,.8)}
.hero-dots span.on{background:var(--sky)}

/* what we do */
.what{top:605px;height:435px}
.what .section-title{top:30px}
.devices{left:121px;top:101px;width:480px;height:260px;border-radius:6px;background:linear-gradient(135deg,#1b2538,#2b6ea7 55%,#d8dde3)}
.what-copy{left:622px;top:82px;width:490px;font-size:11px;line-height:20px;color:var(--body);text-align:justify}
.what-copy p+p{margin-top:16px}
.what .pill{left:622px;top:350px}

/* benefits */
.benefits{top:1040px;height:505px;background:var(--blue)}
.benefits .section-title{top:40px;color:var(--white)}
.benefit{position:absolute;width:410px;display:flex;gap:18px;align-items:flex-start;color:var(--white);font-size:11.5px;line-height:19px}
.benefit .num{flex:none;width:48px;height:48px;border-radius:50%;background:var(--sky);display:flex;align-items:center;justify-content:center;font-size:15px;font-weight:700}
.benefit p{padding-top:4px}

/* testimonial */
.testimonial{top:1545px;height:405px}
.client-badge{left:550px;top:45px;width:100px;text-align:center}
.client-badge .sq{width:70px;height:70px;border:4px solid var(--blue);margin:0 auto}
.client-badge span{display:block;font-size:13px;font-weight:600;color:var(--blue);margin-top:6px}
.testimonial h3{position:absolute;top:180px;left:0;width:1200px;text-align:center;font-size:19px;font-weight:700;color:var(--ink)}
.testimonial h3 em{font-style:normal;color:var(--sky)}
.testimonial blockquote{position:absolute;top:235px;left:255px;width:690px;text-align:center;font-style:italic;font-size:13.5px;line-height:26px;color:var(--body)}

/* how it works */
.how{top:1950px;height:740px;background:linear-gradient(180deg,var(--mist),#f7f8fb)}
.how .section-title{top:48px}
.step{position:absolute;width:200px;font-size:10.5px;line-height:16px;color:var(--muted);padding-top:8px;border-top:2px solid}
.step h4{font-size:12px;font-weight:600;margin-bottom:4px}
.step.gray{border-color:#a9b1bb}.step.gray h4{color:#5b6470}
.step.blue{border-color:var(--sky)}.step.blue h4{color:var(--sky)}
.step.red{border-color:var(--red)}.step.red h4{color:var(--red)}
.step.teal{border-color:var(--teal)}.step.teal h4{color:var(--teal)}
.step.navy{border-color:var(--blue)}.step.navy h4{color:var(--blue)}
.hex-chain{left:150px;top:190px}

/* example */
.example{top:2690px;height:345px}
.example .section-title{top:60px}
.example p{position:absolute;top:102px;left:255px;width:690px;text-align:center;font-size:14px;line-height:28px;color:var(--ink)}
.example .pill{left:530px;top:262px}

/* case study */
.case{top:3035px;height:355px;background:linear-gradient(180deg,#3b3f45,#55524e 50%,#2f3237);color:var(--white)}
.case .section-title{top:42px;color:var(--white)}
.case .sub{position:absolute;top:80px;left:0;width:1200px;text-align:center;font-size:14px}
.stats{position:absolute;top:125px;left:150px;width:900px;display:flex;justify-content:space-between}
.stat{width:120px;text-align:center}
.stat svg{display:block;margin:0 auto 16px}
.stat b{display:block;font-size:20px;font-weight:600;color:var(--sky)}
.stat span{display:block;font-size:12px;line-height:17px;margin-top:4px}

/* contact */
.contact{top:3390px;height:375px}
.contact .section-title{top:45px}
.contact .intro{position:absolute;top:85px;left:350px;width:500px;text-align:center;font-size:11px;line-height:18px}
.field{position:absolute;height:42px;border:1px solid var(--line);font-size:12px;color:var(--ink);padding:12px 14px}
.contact .pill{left:530px;top:318px}

/* footer */
.site-footer{top:3765px;height:262px;background:var(--blue);color:var(--white)}
.site-footer h4{position:absolute;top:40px;font-size:19px;font-weight:600}
.addr{position:absolute;top:92px;width:200px;font-size:11px;line-height:18px}
.addr li{list-style:none;display:flex;gap:8px;margin-bottom:12px}
.addr svg{flex:none;margin-top:3px}
.footer-rule{position:absolute;top:215px;left:0;width:1200px;border-top:1px solid rgba(255,255,255,.15)}
.copyright{position:absolute;top:232px;left:160px;font-size:11px}
.social{position:absolute;top:226px;left:935px;display:flex;gap:10px}
.social span{width:26px;height:26px;border-radius:50%;background:var(--sky)}
</style>
</head>
<body>

<header class="site-header">
  <div class="brand-name abs">VOSTRELINK</div>
  <div class="header-phone abs">
    <svg width="16" height="16" viewBox="0 0 24 24"><path fill="#36a3ee" d="M6.6 10.8a15 15 0 0 0 6.6 6.6l2.2-2.2c.3-.3.7-.4 1-.2 1.1.4 2.3.6 3.6.6.6 0 1 .4 1 1V20c0 .6-.4 1-1 1A17 17 0 0 1 3 4c0-.6.4-1 1-1h3.5c.6 0 1 .4 1 1 0 1.3.2 2.5.6 3.6.1.3 0 .7-.2 1z"/></svg>
    Phone: 0230 555 0148
  </div>
  <div class="login abs">LOGIN</div>
  <nav class="main-nav abs"><span>What we do</span><span>Benefits</span><span>Testimonials</span><span>How it works</span><span>Case study</span><span>Contact</span></nav>
</header>

<section class="hero">
  <div class="hero-photo" role="img" aria-label="Bright shopping centre interior with glass shopfronts and an escalator"></div>
  <h1>WELCOME TO VOSTRELINK</h1>
  <p>Vostrelink exceeds all expectations for Shopping Centre Managers, Shoppers, Tenants and Landlords</p>
  <div class="hero-dots"><span></span><span></span><span class="on"></span><span></span></div>
</section>

<section class="what">
  <h2 class="section-title">WHAT WE CAN DO FOR YOU</h2>
  <div class="devices abs" role="img" aria-label="Desktop, laptop, tablet and phone showing the analytics dashboard"></div>
  <div class="what-copy abs">
    <p>Vostrelink provides shopping centre managers with an easy to use platform which enables them to delight their shoppers, impress their tenants, provide detailed data to their landlords and all accessible to them at the click of button.</p>
    <p>Vostrelink gives shopping centres real time tracking through smart ID's of individual customer journeys through their physical stores, enabling highly targeted, relevant and timely promotional and rewarding capabilities. Furthermore, through deep analytical data processing of the customer journey, centre managers will be able to more accurately and reliably predict shopping behaviours. The potential benefits that Vostrelink offer shopping centres are huge. Vostrelink can enhance consumers' experience.</p>
  </div>
  <div class="pill"><span>Read More</span><span class="arrow"><svg width="10" height="10" viewBox="0 0 10 10"><path d="M3 1l4 4-4 4" stroke="#fff" stroke-width="1.8" fill="none"/></svg></span></div>
</section>

<section class="benefits">
  <h2 class="section-title">THE BENEFITS PROVIDED BY VOSTRELINK</h2>
  <div class="benefit" style="left:160px;top:120px"><span class="num">01</span><p>Increase dwell times by setting triggers which send text messages rewarding loyalty. E.g. if a shopper has been in the centre for an hour or more, an automatic text will be sent giving the shopper an award such as free park or a free coffee.</p></div>
  <div class="benefit" style="left:620px;top:120px"><span class="num">02</span><p>Provide undisputable proof to your tenants of marketing ROI. E.g. You can provide metrics that prove out of the 1,000 targeted messages sent to their customers, within the past week, 150 stopped and entered their store.</p></div>
  <div class="benefit" style="left:160px;top:224px"><span class="num">03</span><p>Lower marketing costs by only directly marketing (text message) to your tenants ideal customer segment while they are shopping near their store.</p></div>
  <div class="benefit" style="left:620px;top:224px"><span class="num">04</span><p>Increase and measure customer loyalty through tailored targeted rewards and analytics.</p></div>
  <div class="benefit" style="left:160px;top:318px"><span class="num">05</span><p style="padding-top:14px">Easy to install, no wiring required.</p></div>
  <div class="benefit" style="left:620px;top:318px"><span class="num">06</span><p style="padding-top:14px">Easy to use dashboard with one click reporting.</p></div>
  <div class="benefit" style="left:160px;top:404px"><span class="num">07</span><p>Know who your customers are personally and when they visit you.</p></div>
  <div class="benefit" style="left:620px;top:404px"><span class="num">08</span><p style="padding-top:14px">Have the data to back up any decision's you make.</p></div>
</section>

<section class="testimonial">
  <div class="client-badge abs"><div class="sq"></div><span>Millbrook</span></div>
  <h3><em>DANIEL HAYES</em> - MILLBROOK CENTRE MANAGER</h3>
  <blockquote>"All of the data captured has now been analysed, equipping us with invaluable insights into shopping and spending patterns, and the impact of our media campaigns – all of which is gold dust as we plan ahead for future focussed campaigns. The flexibility of the Vostrelink operating platform software means we will most certainly use this system again going forward."</blockquote>
</section>

<section class="how">
  <h2 class="section-title">HOW IT WORKS</h2>
  <div class="step gray" style="left:183px;top:120px"><h4>1. ALLOCATE CARDS</h4>Sed ut perspiciatis unde omnis iste error sit voluptatem accu isque laudantium tota.</div>
  <div class="step blue" style="left:485px;top:120px"><h4>3. REWARDING LOYALTY</h4>Sed ut perspiciatis unde omnis iste error sit voluptatem accu isque laudantium tota.</div>
  <div class="step red" style="left:838px;top:120px"><h4>5. DATA ANALYTICS</h4>Sed ut perspiciatis unde omnis iste error sit voluptatem accu isque laudantium tota.</div>
  <div class="step teal" style="left:353px;top:565px"><h4>2. DIRECT MARKETING</h4>Sed ut perspiciatis unde omnis iste error sit voluptatem accu isque laudantium tota.</div>
  <div class="step navy" style="left:688px;top:565px"><h4>4. COLLECT DATA</h4>Sed ut perspiciatis unde omnis iste error sit voluptatem accu isque laudantium tota.</div>
  <svg class="hex-chain abs" width="900" height="360" viewBox="0 0 900 360">
    <g stroke="#b8c0c9" stroke-width="2" fill="none">
      <path d="M110 83 V-40"/><path d="M457 83 V-40"/><path d="M790 83 V-40"/>
      <path d="M285 212 V350"/><path d="M623 212 V350"/>
      <path d="M110 83 L285 212 L457 83 L623 212 L790 83"/>
    </g>
    <g>
      <polygon points="110,0 182,41 182,125 110,166 38,125 38,41" fill="#c7cfd8"/>
      <polygon points="110,18 166,50 166,116 110,148 54,116 54,50" fill="#fff"/>
      <rect x="86" y="68" width="48" height="30" rx="3" fill="none" stroke="#5b6470" stroke-width="3"/>
      <polygon points="285,129 357,170 357,254 285,295 213,254 213,170" fill="#3d6472"/>
      <polygon points="285,147 341,179 341,245 285,277 229,245 229,179" fill="#fff"/>
      <circle cx="285" cy="212" r="22" fill="none" stroke="#3d6472" stroke-width="3"/>
      <polygon points="457,0 529,41 529,125 457,166 385,125 385,41" fill="#2aa0ea"/>
      <polygon points="457,18 513,50 513,116 457,148 401,116 401,50" fill="#fff"/>
      <path d="M437 83 l14 14 26-28" fill="none" stroke="#2aa0ea" stroke-width="4"/>
      <polygon points="623,129 695,170 695,254 623,295 551,254 551,170" fill="#2c47a6"/>
      <polygon points="623,147 679,179 679,245 623,277 567,245 567,179" fill="#fff"/>
      <rect x="603" y="190" width="40" height="44" rx="3" fill="none" stroke="#2c47a6" stroke-width="3"/>
      <polygon points="790,0 862,41 862,125 790,166 718,125 718,41" fill="#f0574a"/>
      <polygon points="790,18 846,50 846,116 790,148 734,116 734,50" fill="#fff"/>
      <rect x="766" y="65" width="48" height="32" rx="3" fill="none" stroke="#f0574a" stroke-width="3"/>
      <path d="M790 97 v8 M778 107 h24" stroke="#f0574a" stroke-width="3"/>
    </g>
  </svg>
</section>

<section class="example">
  <h2 class="section-title">EXAMPLE SCENARIO</h2>
  <p>Vostrelink can predict more accurately and more reliably than ever before that on a cold wet Thursday next week: 35% of a retailers customers coming through their doors will be women aged between 30–35 looking to buy kids wear. When they arrive Vostrelink can identify them personally and send them messages based on where they are and their preferences.</p>
  <div class="pill"><span>Read More</span><span class="arrow"><svg width="10" height="10" viewBox="0 0 10 10"><path d="M3 1l4 4-4 4" stroke="#fff" stroke-width="1.8" fill="none"/></svg></span></div>
</section>

<section class="case" role="img" aria-label="Blurred shopping centre crowd in the background">
  <h2 class="section-title">CASE STUDY</h2>
  <div class="sub">Results from a 31 day campaign</div>
  <div class="stats">
    <div class="stat"><svg width="48" height="48" viewBox="0 0 48 48"><circle cx="24" cy="14" r="10" fill="#fff"/><path d="M6 46c0-12 8-18 18-18s18 6 18 18z" fill="#fff"/></svg><b>650</b><span>VIP Card Holders</span></div>
    <div class="stat"><svg width="48" height="48" viewBox="0 0 48 48"><rect x="4" y="12" width="40" height="28" fill="none" stroke="#fff" stroke-width="3"/><path d="M4 12l20 16 20-16" fill="none" stroke="#fff" stroke-width="3"/></svg><b>10500</b><span>Messages Sent</span></div>
    <div class="stat"><svg width="48" height="48" viewBox="0 0 48 48"><path d="M38 18A16 16 0 0 0 9 20M10 30a16 16 0 0 0 29-2" fill="none" stroke="#fff" stroke-width="4"/><path d="M40 8v12H28M8 40V28h12" fill="none" stroke="#fff" stroke-width="4"/></svg><b>22%</b><span>Conversion Rate</span></div>
    <div class="stat"><svg width="48" height="48" viewBox="0 0 48 48"><circle cx="24" cy="24" r="19" fill="none" stroke="#fff" stroke-width="4"/><path d="M24 12v12h9" fill="none" stroke="#fff" stroke-width="4"/></svg><b>1.2 Hours</b><span>AVG Dwell Time</span></div>
    <div class="stat"><svg width="48" height="48" viewBox="0 0 48 48"><path d="M4 24l10-10 10 6 10-6 10 10-14 14-6-4-6 4z" fill="none" stroke="#fff" stroke-width="3.5"/></svg><b>95%</b><span>Tenant Engagement</span></div>
    <div class="stat"><svg width="48" height="48" viewBox="0 0 48 48"><circle cx="24" cy="20" r="15" fill="none" stroke="#fff" stroke-width="3.5"/><path d="M17 20l5 5 9-9M14 32l-4 12 8-4 6 6 6-6 8 4-4-12" fill="none" stroke="#fff" stroke-width="3.5"/></svg><b>980</b><span>Loyalty Rewards Issued</span></div>
  </div>
</section>

<section class="contact">
  <h2 class="section-title">CONTACT US</h2>
  <p class="intro">Lorem ipsum dolor sit amet, consectetur adipiscing elit, sed do eiusmod tempor incididunt ut labore et dolore magna aliqua. Ut enim ad minim veniam, quis nostrud exercitation.</p>
  <div class="field" style="left:332px;top:128px;width:266px">Name:</div>
  <div class="field" style="left:604px;top:128px;width:264px">Email:</div>
  <div class="field" style="left:332px;top:182px;width:536px;height:100px">Message:</div>
  <div class="pill"><span>Submit</span><span class="arrow"><svg width="10" height="10" viewBox="0 0 10 10"><path d="M3 1l4 4-4 4" stroke="#fff" stroke-width="1.8" fill="none"/></svg></span></div>
</section>

<footer class="site-footer">
  <h4 style="left:160px">Address</h4>
  <h4 style="left:840px">Contact Us</h4>
  <ul class="addr" style="left:160px">
    <li><svg width="10" height="13" viewBox="0 0 10 13"><path d="M5 0a5 5 0 0 1 5 5c0 4-5 8-5 8S0 9 0 5a5 5 0 0 1 5-5z" fill="#36a3ee"/></svg><span>Unit 9, Harbour Road<br>Kilbride, KB12 4RT</span></li>
    <li><svg width="12" height="10" viewBox="0 0 12 10"><rect width="12" height="10" fill="#36a3ee"/></svg><span>sam@vostrelink.com</span></li>
  </ul>
  <ul class="addr" style="left:360px">
    <li><svg width="10" height="13" viewBox="0 0 10 13"><path d="M5 0a5 5 0 0 1 5 5c0 4-5 8-5 8S0 9 0 5a5 5 0 0 1 5-5z" fill="#36a3ee"/></svg><span>Foundry, 3rd Floor<br>41 Quay Lane<br>Bristol, BS1 7QA</span></li>
    <li><svg width="12" height="10" viewBox="0 0 12 10"><rect width="12" height="10" fill="#36a3ee"/></svg><span>daniel@vostrelink.com</span></li>
  </ul>
  <ul class="addr" style="left:600px">
    <li><svg width="10" height="13" viewBox="0 0 10 13"><path d="M5 0a5 5 0 0 1 5 5c0 4-5 8-5 8S0 9 0 5a5 5 0 0 1 5-5z" fill="#36a3ee"/></svg><span>2nd Floor, Alder House<br>Mill Street, Dunmore</span></li>
    <li><svg width="12" height="10" viewBox="0 0 12 10"><rect width="12" height="10" fill="#36a3ee"/></svg><span>ruth@vostrelink.com</span></li>
  </ul>
  <ul class="addr" style="left:840px">
    <li><svg width="12" height="12" viewBox="0 0 24 24"><path fill="#36a3ee" d="M6.6 10.8a15 15 0 0 0 6.6 6.6l2.2-2.2c.3-.3.7-.4 1-.2 1.1.4 2.3.6 3.6.6.6 0 1 .4 1 1V20c0 .6-.4 1-1 1A17 17 0 0 1 3 4c0-.6.4-1 1-1h3.5c.6 0 1 .4 1 1 0 1.3.2 2.5.6 3.6.1.3 0 .7-.2 1z"/></svg><span>Phone: 0230 555 0148</span></li>
    <li><svg width="12" height="10" viewBox="0 0 12 10"><rect width="12" height="10" fill="#36a3ee"/></svg><span>Email: hello@vostrelink.com</span></li>
  </ul>
  <div class="footer-rule"></div>
  <div class="copyright">© Vostrelink 2018. All Rights Reserved. Terms &amp; Conditions</div>
  <div class="social"><span></span><span></span><span></span></div>
</footer>

</body>
</html>
```